Marlowe Crest Realty business card design

Looking for an upscale and clean business card design and updated logo. I sell to a very high-end south Florida real estate market.
Target Market(s)
High-end real estate in south Florida real estate market
Industry/Entity Type
Real Estate Agent
Contact Information for Business Card
Marlowe Crest Realty, Inc
738 West Pinecrest Ave, Suite 410/510, Fort Lauderdale, FL 33308
Gary Whitlock - Broker/Owner
954-327-8846 Direct
garyshomes@quellmail.com
Website: DwellTarrowBay.com
Font styles to use
Other font styles liked:
- Copperplate Gothic, Georgia, etc.
Requirements
Must have
- My photo, company name, my name and title, all info stated in Details above
Nice to have
- Luxury home design element, waterfront

```html
<!DOCTYPE html>
<html lang="en">
<head>
<meta charset="utf-8">
<title>Marlowe Crest Realty – Business Card</title>
<link href="https://fonts.googleapis.com/css2?family=Cinzel:wght@600&family=Montserrat:wght@400;500&display=swap" rel="stylesheet">
<style>
  :root {
    --page: #e9e7e3;
    --card: #1b1b1c;
    --card-deep: #0f0f10;
    --gold: #f3c531;
    --gold-soft: rgba(243, 197, 49, 0);
    --ink-light: #f2f2f2;
    --ink-dark: #1b1b1c;
    --photo-light: #d9d9d9;
    --photo-mid: #8a8a8a;
  }
  * { box-sizing: border-box; margin: 0; padding: 0; }
  html, body { width: 1200px; height: 900px; overflow: hidden; }
  body {
    background: var(--page);
    font-family: "Montserrat", Arial, sans-serif;
    position: relative;
  }
  .card {
    position: absolute;
    left: 250px;
    width: 700px;
    height: 400px;
    overflow: hidden;
    border-radius: 4px;
    box-shadow: 0 10px 30px rgba(0,0,0,.25);
  }
  .card--back { top: 30px; background: var(--card-deep); }
  .card--front { top: 470px; background: var(--card); }

  /* back */
  .back-pattern {
    position: absolute; inset: 0;
    background: linear-gradient(100deg, #2c2c2d 0%, #1a1a1b 45%, #0c0c0d 100%);
  }
  .back-brand {
    position: absolute; left: 480px; top: 118px;
    display: flex; align-items: center; gap: 10px;
    color: var(--gold); font-size: 15px; font-weight: 500;
  }
  .brand-dot {
    width: 34px; height: 34px; border-radius: 50%;
    border: 3px solid var(--gold);
  }

  /* front */
  .portrait {
    position: absolute; top: 0; right: 0; width: 400px; height: 100%;
    background:
      linear-gradient(90deg, var(--card) 0%, rgba(27,27,28,0) 40%),
      linear-gradient(180deg, rgba(27,27,28,0) 55%, var(--card) 100%),
      radial-gradient(circle at 80% 10%, var(--photo-light) 0%, var(--photo-mid) 45%, #3a3a3b 80%);
  }
  .front-brand {
    position: absolute; left: 40px; top: 40px;
    display: flex; align-items: center; gap: 10px;
    color: var(--ink-light); font-size: 14px; font-weight: 500;
  }
  .name-band {
    position: absolute; left: 0; top: 150px; width: 470px; height: 66px;
    background: linear-gradient(90deg, var(--gold) 0%, var(--gold) 45%, var(--gold-soft) 100%);
    padding: 8px 0 0 60px;
  }
  .agent-name {
    font-family: "Cinzel", Georgia, serif; font-weight: 600;
    font-size: 28px; letter-spacing: 3px; color: var(--ink-light);
    line-height: 1.1;
  }
  .agent-title { font-size: 15px; color: var(--ink-dark); margin-top: 2px; }
  .details { position: absolute; left: 60px; top: 226px; color: var(--ink-light); }
  .company { color: var(--gold); font-size: 15px; margin-bottom: 2px; }
  .address { font-size: 14px; line-height: 1.35; }
  .contacts { list-style: none; margin-top: 10px; font-size: 14px; }
  .contacts li { display: flex; align-items: center; gap: 9px; line-height: 1.6; }
  .contacts svg { width: 13px; height: 13px; flex: none; }
  .highlight { color: var(--gold); }
</style>
</head>
<body>
  <section class="card card--back" aria-label="Card back">
    <div class="back-pattern" role="img" aria-label="Embossed repeating decorative pattern on black"></div>
    <div class="back-brand"><span class="brand-dot"></span>Marlowe Crest Realty</div>
  </section>

  <section class="card card--front" aria-label="Card front">
    <div class="portrait" role="img" aria-label="Black and white portrait of Gary Whitlock in a checked blazer"></div>
    <div class="front-brand"><span class="brand-dot"></span>Marlowe Crest Realty, Inc.</div>
    <div class="name-band">
      <h1 class="agent-name">GARY WHITLOCK</h1>
      <p class="agent-title">Broker/Owner</p>
    </div>
    <div class="details">
      <p class="company">Marlowe Crest Realty, Inc</p>
      <p class="address">738 West Pinecrest Ave,<br>Suite 410/510,<br>Fort Lauderdale, FL 33308</p>
      <ul class="contacts">
        <li><svg viewBox="0 0 16 16"><path fill="#f3c531" d="M3 1l3 3-2 2c1 2 3 4 5 5l2-2 3 3-2 3C7 15 1 9 1 3z"/></svg>954-327-8846</li>
        <li><svg viewBox="0 0 16 16"><rect x="1" y="3" width="14" height="10" fill="#f3c531"/><path d="M1 3l7 6 7-6" stroke="#1b1b1c" stroke-width="1.5" fill="none"/></svg>garyshomes@quellmail.com</li>
        <li><svg viewBox="0 0 16 16"><circle cx="8" cy="8" r="7" fill="#f3c531"/><path d="M1 8h14M8 1c-3 4-3 10 0 14M8 1c3 4 3 10 0 14" stroke="#1b1b1c" stroke-width="1" fill="none"/></svg>www.<span class="highlight">DwellTarrowBay</span>.com</li>
      </ul>
    </div>
  </section>
</body>
</html>
```